BRIGHT RIVER POWER.

I'd like my business logo.
contact name: Dennis Halvorsen
phone:0438759164
email: info@brightriverpower.net.au
website: www.brightriverpower.net.au

services:
solar
battery storage
LED lighting
energy saving solutions
general electrical
I'd like the design to look professional

Target Market(s)

Everyone

Industry/Entity Type

Business

Contact Information for Business Card

as described above

Requirements
Must have
• Id like the colours and the design to work well with my logo.

```html
<!DOCTYPE html>
<html lang="en">
<head>
<meta charset="utf-8">
<title>Bright River Power – Business Card</title>
<link rel="stylesheet" href="https://fonts.googleapis.com/css2?family=Source+Sans+3:ital,wght@0,400;0,600;1,400&display=swap">
<style>
  :root {
    --bg: #e9e9e9;
    --card: #ffffff;
    --green: #4ea82a;
    --green-light: #8cc63e;
    --orange: #f7941d;
    --orange-light: #fbb03b;
    --text: #333333;
    --text-soft: #555555;
  }
  * { margin: 0; padding: 0; box-sizing: border-box; }
  html, body { width: 1105px; height: 1200px; overflow: hidden; }
  body {
    background: var(--bg);
    font-family: "Source Sans 3", sans-serif;
    position: relative;
  }
  .card {
    position: absolute;
    left: 193px;
    width: 720px;
    height: 412px;
    background: var(--card);
    box-shadow: 0 2px 8px rgba(0,0,0,0.12);
    overflow: hidden;
  }
  .card--front { top: 167px; }
  .card--back { top: 623px; }

  .brand {
    position: absolute;
    top: 80px;
    left: 0; right: 0;
    display: flex;
    align-items: center;
    justify-content: center;
    gap: 16px;
  }
  .brand__dot {
    width: 56px; height: 56px;
    border-radius: 50%;
    background: var(--green);
  }
  .brand__name {
    font-weight: 600;
    font-size: 40px;
    letter-spacing: 1px;
    color: var(--green);
  }
  .contact-name {
    position: absolute;
    top: 243px;
    left: 0; right: 0;
    text-align: center;
    font-weight: 600;
    font-size: 27px;
    color: var(--green);
  }
  .contact-lines {
    position: absolute;
    top: 290px;
    left: 0; right: 0;
    display: flex;
    justify-content: center;
    gap: 22px;
    font-size: 19px;
    color: var(--text-soft);
  }
  .contact-lines__item { display: flex; align-items: center; gap: 7px; }
  .contact-lines__item svg { fill: var(--green); }

  .web-band {
    position: absolute;
    left: 0; right: 0;
    top: 373px;
    height: 39px;
    background: linear-gradient(90deg, var(--orange) 0%, var(--orange-light) 12%, var(--green-light) 40%, var(--green) 100%);
  }
  .web-band__dot {
    position: absolute;
    left: 117px; top: 5px;
    width: 29px; height: 29px;
    border-radius: 50%;
    background: var(--card);
  }
  .web-band__url {
    position: absolute;
    left: 220px; top: 6px;
    font-size: 20px;
    letter-spacing: 3.6px;
    color: var(--card);
  }

  .back-mark {
    position: absolute;
    left: 110px; top: 110px;
    width: 200px;
    display: flex;
    flex-direction: column;
    align-items: center;
    gap: 14px;
  }
  .back-mark__dot {
    width: 140px; height: 140px;
    border-radius: 50%;
    background: var(--green);
  }
  .back-mark__name {
    font-weight: 600;
    font-size: 18px;
    letter-spacing: 0.5px;
    color: var(--green);
    white-space: nowrap;
  }
  .services {
    position: absolute;
    left: 370px; top: 136px;
    list-style: none;
  }
  .services__item {
    display: flex;
    align-items: center;
    gap: 11px;
    height: 35.5px;
    font-style: italic;
    font-size: 21px;
    color: var(--text);
  }
  .services__item::before {
    content: "";
    width: 8px; height: 8px;
    border-radius: 50%;
    background: var(--green);
  }
</style>
</head>
<body>
  <section class="card card--front">
    <div class="brand">
      <span class="brand__dot"></span>
      <span class="brand__name">BRIGHT RIVER POWER</span>
    </div>
    <p class="contact-name">Dennis Halvorsen</p>
    <div class="contact-lines">
      <span class="contact-lines__item">
        <svg width="17" height="17" viewBox="0 0 24 24" aria-hidden="true"><path d="M6.6 10.8a15.1 15.1 0 0 0 6.6 6.6l2.2-2.2a1 1 0 0 1 1-.25 11.4 11.4 0 0 0 3.6.57 1 1 0 0 1 1 1V20a1 1 0 0 1-1 1A17 17 0 0 1 3 4a1 1 0 0 1 1-1h3.5a1 1 0 0 1 1 1c0 1.25.2 2.45.57 3.57a1 1 0 0 1-.25 1z"/></svg>
        0438759164
      </span>
      <span class="contact-lines__item">
        <svg width="18" height="13" viewBox="0 0 18 13" aria-hidden="true"><path d="M0 0h18v13H0z M1.5 1.5 9 7l7.5-5.5" fill="var(--green)" stroke="#fff" stroke-width="1.3"/></svg>
        info@brightriverpower.net.au
      </span>
    </div>
    <div class="web-band">
      <span class="web-band__dot"></span>
      <span class="web-band__url">brightriverpower.net.au</span>
    </div>
  </section>

  <section class="card card--back">
    <div class="back-mark">
      <span class="back-mark__dot"></span>
      <span class="back-mark__name">BRIGHT RIVER POWER</span>
    </div>
    <ul class="services">
      <li class="services__item">Solar</li>
      <li class="services__item">Battery storage</li>
      <li class="services__item">LED lighting</li>
      <li class="services__item">Energy saving solutions</li>
    </ul>
  </section>
</body>
</html>
```